Medical Clinic Group Looking for Website Design

We own and operate medical clinics and are looking looking to revamp our website. Our current website is www.brightpathcareclinics.ca We need our website to be more functional, user friendly, and easier to maintain.

```html
<!DOCTYPE html>
<html lang="en">
<head>
<meta charset="UTF-8">
<title>BrightPath Care Clinics</title>
<link href="https://fonts.googleapis.com/css2?family=Poppins:wght@400;500;600&family=Roboto:wght@300;400&display=swap" rel="stylesheet">
<style>
:root{
  --teal:#33d2dd;
  --teal-dark:#1fb6c2;
  --grey:#79797b;
  --grey-ring:#8e8e90;
  --ink:#111;
  --white:#fff;
  --black:#000;
}
*{margin:0;padding:0;box-sizing:border-box}
html,body{width:1200px;height:3201px;overflow:hidden;background:var(--white)}
body{position:relative;font-family:'Roboto',sans-serif;color:var(--ink)}
.abs{position:absolute}
.topbar{left:0;top:0;width:1200px;height:47px;background:var(--teal);color:var(--white);font-size:15px;font-family:'Roboto',sans-serif}
.topbar .item{position:absolute;top:14px;display:flex;align-items:center;gap:12px}
.topbar svg{width:20px;height:20px;fill:var(--white)}
.nav{left:0;top:47px;width:1200px;height:78px;background:var(--white);box-shadow:0 1px 3px rgba(0,0,0,.08)}
.brand{position:absolute;display:flex;align-items:center;gap:10px;font-family:'Poppins',sans-serif;font-weight:400}
.brand .dot{border-radius:50%;border:3px solid #9a9a9a}
.nav .brand{left:112px;top:20px;font-size:30px;color:var(--teal)}
.nav .brand .dot{width:36px;height:36px}
.menu{position:absolute;left:393px;top:29px;display:flex;gap:46px;font-family:'Poppins',sans-serif;font-size:16px;color:#222}
.menu .active{color:var(--teal);font-weight:500;border-bottom:2px solid var(--teal);padding-bottom:3px}
.hero{left:0;top:125px;width:1200px;height:670px;background:linear-gradient(90deg,#c9c4bd 0%,#e4e2de 40%,#eceef0 60%,#c8ccd0 100%)}
.hero-text{left:0;top:300px;width:1200px;text-align:center;color:var(--white)}
.hero-text h1{font-family:'Poppins',sans-serif;font-weight:600;font-size:52px;line-height:55px;text-shadow:0 2px 6px rgba(0,0,0,.35)}
.hero-text p{margin-top:16px;font-size:15px;text-transform:uppercase;text-shadow:0 1px 3px rgba(0,0,0,.4)}
.btn{display:inline-block;background:linear-gradient(180deg,var(--teal),#2db4bf);color:var(--white);font-family:'Poppins',sans-serif;font-weight:500}
.hero-text .btn{margin-top:25px;font-size:19px;padding:12px 20px}
.section-h2{font-family:'Poppins',sans-serif;font-weight:500}
.about{left:111px;top:862px;width:470px}
.about h3{font-family:'Poppins',sans-serif;font-weight:500;font-size:32px}
.about h2{font-size:34px;color:#555;margin-top:2px}
.about h2 span{color:var(--teal)}
.about p{margin-top:6px;font-size:15px;line-height:31px;color:#222}
.about .btn{margin-top:27px;font-size:19px;padding:13px 18px}
.diamond{left:598px;top:870px;width:495px;height:388px}
.features{left:0;top:1349px;width:1200px;height:351px;background:var(--grey)}
.feature{position:absolute;top:74px;width:220px;text-align:center;color:var(--white);font-family:'Poppins',sans-serif;font-weight:500;font-size:21px}
.feature .ring{width:145px;height:145px;border-radius:50%;background:var(--grey-ring);margin:0 auto;display:flex;align-items:center;justify-content:center}
.feature .core{width:123px;height:123px;border-radius:50%;background:var(--teal);display:flex;align-items:center;justify-content:center}
.feature svg{width:80px;height:80px;fill:none;stroke:var(--white);stroke-width:3.5;stroke-linecap:round;stroke-linejoin:round}
.feature span{display:block;margin-top:10px}
.arrow{position:absolute;top:156px;width:40px;height:40px;border-radius:50%;display:flex;align-items:center;justify-content:center}
.arrow svg{width:18px;height:18px;fill:none;stroke-width:2.5}
.services-title{left:0;top:1760px;width:1200px;text-align:center;font-size:32px}
.card{position:absolute;top:1850px;width:277px;height:307px;background:var(--white);border-radius:8px;box-shadow:0 3px 8px rgba(0,0,0,.15);overflow:hidden;text-align:center;font-family:'Poppins',sans-serif;font-weight:500;font-size:21px}
.card .photo{height:234px}
.card .label{padding-top:22px}
.card.active{background:var(--teal);color:var(--white)}
.promo{left:0;top:2235px;width:1200px;height:520px;background:var(--teal)}
.promo-photo{left:114px;top:2260px;width:360px;height:360px;border-radius:50%;border:9px solid var(--white);background:linear-gradient(160deg,#f2f3f3,#d8dadb 60%,#7f9cc4)}
.promo-text{left:514px;top:2308px;width:540px;color:var(--white)}
.promo-text h4{font-family:'Poppins',sans-serif;font-weight:500;font-size:19px}
.promo-text h2{font-size:32px;margin-top:10px}
.promo-text p{margin-top:12px;font-size:15px;line-height:31px}
.footer{left:0;top:2740px;width:1200px;height:461px;background:var(--black);color:var(--white)}
.field{position:absolute;top:34px;width:192px;height:63px;border:2px solid var(--white);padding:21px 20px;font-family:'Poppins',sans-serif;font-size:16px}
.subscribe{position:absolute;left:898px;top:34px;width:192px;height:63px;background:var(--teal);border:2px solid var(--white);text-align:center;line-height:59px;font-family:'Poppins',sans-serif;font-weight:500;font-size:20px}
.footer .brand{left:111px;top:134px;font-size:28px;color:var(--teal)}
.footer .brand .dot{width:38px;height:38px}
.about-foot{left:111px;top:199px;width:275px;font-size:15px;line-height:26px}
.col h5{font-family:'Poppins',sans-serif;font-weight:500;font-size:20px;margin-bottom:4px}
.col li{list-style:none;font-size:15px;line-height:26px}
.contact-row{display:flex;gap:11px;font-size:15px;line-height:26px;margin-top:10px}
.contact-row i{flex:none;width:33px;height:33px;border-radius:50%;background:var(--teal);display:flex;align-items:center;justify-content:center}
.contact-row svg{width:16px;height:16px;fill:var(--white)}
.rule{left:111px;top:389px;width:978px;height:1px;background:#444}
.copy{left:0;top:418px;width:1200px;text-align:center;font-size:15px}
</style>
</head>
<body>

<header class="abs topbar">
  <div class="item" style="left:112px"><svg viewBox="0 0 24 24"><path d="M6.6 10.8a15 15 0 0 0 6.6 6.6l2.2-2.2a1 1 0 0 1 1-.25 11.4 11.4 0 0 0 3.6.57 1 1 0 0 1 1 1V20a1 1 0 0 1-1 1A17 17 0 0 1 3 4a1 1 0 0 1 1-1h3.5a1 1 0 0 1 1 1c0 1.25.2 2.45.57 3.57a1 1 0 0 1-.25 1z"/></svg>604.555.0147</div>
  <div class="item" style="left:278px"><svg viewBox="0 0 24 24"><path d="M2 5h20v14H2z M2 6l10 7 10-7" /></svg>hello@brightpathcareclinics.ca</div>
  <div class="item" style="left:826px"><svg viewBox="0 0 24 24"><path d="M12 2a7 7 0 0 0-7 7c0 5 7 13 7 13s7-8 7-13a7 7 0 0 0-7-7zm0 9.5A2.5 2.5 0 1 1 12 6.5a2.5 2.5 0 0 1 0 5z"/></svg>BrightPath Care Clinics, Canada.</div>
</header>

<nav class="abs nav">
  <div class="brand"><span class="dot"></span>brightpath</div>
  <div class="menu">
    <span class="active">Home</span><span>About Us</span><span>Locations</span><span>For Patients</span><span>For Providers</span><span>Book Online</span>
  </div>
</nav>

<section class="abs hero" role="img" aria-label="Photo of a patient consulting with a doctor at a clinic desk"></section>
<svg class="abs" style="left:0;top:680px" width="1200" height="140" viewBox="0 0 1200 140" aria-hidden="true">
  <path d="M0 10 Q600 120 1200 10 L1200 140 L0 140Z" fill="#7d7d7f"/>
  <path d="M0 22 Q600 130 1200 22 L1200 140 L0 140Z" fill="var(--teal)"/>
  <path d="M0 40 Q600 150 1200 40 L1200 140 L0 140Z" fill="#fff"/>
</svg>
<div class="abs hero-text">
  <h1>Welcome To<br>BrightPath Care</h1>
  <p>Easy access to care when you need it</p>
  <span class="btn">Book An Appoinment</span>
</div>

<section class="abs about">
  <h3>About Us</h3>
  <h2 class="section-h2"><span>Exciting Things</span> Are Happening!</h2>
  <p>Renovations have begun at our Maplewood location! Over the next several months, we will be renovating the entire clinic to serve our existing patients better, as well as to create the space to accommodate several new physicians and specialists. The clinic will remain open while we renovate so please pay attention to the signage guiding you to your physicians assistant.</p>
  <span class="btn">Read More</span>
</section>
<svg class="abs diamond" viewBox="0 0 495 388" role="img" aria-label="Photo of a mother and child on a video call with a doctor">
  <defs><linearGradient id="dg" x1="0" y1="0" x2="1" y2="1"><stop offset="0" stop-color="#d9d4cf"/><stop offset=".5" stop-color="#8b7566"/><stop offset="1" stop-color="#3a3431"/></linearGradient></defs>
  <path d="M0 198 L185 0 L245 55 L295 0 L495 185 L310 388 L255 330 L200 388Z" fill="url(#dg)"/>
</svg>

<section class="abs features">
  <div class="arrow" style="left:37px;background:#a5a5a7"><svg viewBox="0 0 18 18" stroke="#fff"><path d="M12 2 L5 9 L12 16"/></svg></div>
  <div class="feature" style="left:79px"><div class="ring"><div class="core"><svg viewBox="0 0 80 80"><circle cx="40" cy="26" r="13"/><path d="M16 64c0-14 10-22 24-22s24 8 24 22z"/></svg></div></div><span>Find a Provider</span></div>
  <div class="feature" style="left:282px"><div class="ring"><div class="core"><svg viewBox="0 0 80 80"><circle cx="40" cy="40" r="14"/><circle cx="40" cy="40" r="5"/><circle cx="22" cy="20" r="7"/><circle cx="40" cy="14" r="7"/><circle cx="58" cy="20" r="7"/><path d="M12 46c0-8 5-12 12-12M68 46c0-8-5-12-12-12M24 66c2-8 8-12 16-12s14 4 16 12"/></svg></div></div><span>Services</span></div>
  <div class="feature" style="left:482px;width:220px"><div class="ring"><div class="core"><svg viewBox="0 0 80 80"><rect x="14" y="16" width="42" height="48" rx="4"/><path d="M14 28h42M24 10v10M46 10v10M22 38h18M22 48h12"/><circle cx="56" cy="56" r="12"/><path d="M50 56l5 5 8-9"/></svg></div></div><span>Book an Appointment</span></div>
  <div class="feature" style="left:698px"><div class="ring"><div class="core"><svg viewBox="0 0 80 80"><path d="M40 60S22 40 22 28a18 18 0 0 1 36 0c0 12-18 32-18 32z"/><circle cx="40" cy="28" r="7"/><path d="M28 56l12 12 12-12"/></svg></div></div><span>Locations</span></div>
  <div class="feature" style="left:903px"><div class="ring"><div class="core"><svg viewBox="0 0 80 80"><path d="M14 20c0 22 18 42 40 44l6-10-10-8-6 5c-8-4-14-10-17-17l5-6-8-10z"/><rect x="34" y="18" width="36" height="26" rx="2"/><path d="M34 20l18 13 18-13"/></svg></div></div><span>Contact Us</span></div>
  <div class="arrow" style="left:1117px;background:#fff"><svg viewBox="0 0 18 18" stroke="var(--teal)"><path d="M6 2 L13 9 L6 16"/></svg></div>
</section>

<h2 class="abs section-h2 services-title">Our Services</h2>
<div class="card" style="left:111px"><div class="photo" role="img" aria-label="Photo of a physiotherapist treating a patient's knee" style="background:linear-gradient(135deg,#2f57b8,#e9e6e3 45%,#cfc7bf)"></div><div class="label">Sports Medicine</div></div>
<div class="card active" style="left:463px"><div class="photo" role="img" aria-label="Photo of a doctor on a tablet video call" style="background:linear-gradient(135deg,#6c6a66,#e5e3df 45%,#a88a72)"></div><div class="label">Online appointment</div></div>
<div class="card" style="left:814px"><div class="photo" role="img" aria-label="Photo of a smiling nurse in blue scrubs" style="background:linear-gradient(135deg,#d9cfc4,#f2efeb 40%,#3a8fd6)"></div><div class="label">BrightPath Care</div></div>

<section class="abs promo"></section>
<div class="abs promo-photo" role="img" aria-label="Photo of a physiotherapist stretching a patient's leg"></div>
<div class="abs promo-text">
  <h4>WE'RE RENOVATING TO SERVE YOU BETTER</h4>
  <h2 class="section-h2">Exciting Things Are Happening!</h2>
  <p>Renovations have begun at our Maplewood location! Over the next several months, we will be renovating the entire clinic to serve our existing patients better, as well as to create the space to accommodate several new physicians and specialists. The clinic will remain open while we renovate so please pay attention to the signage guiding you to your physicians assistant.</p>
</div>
<svg class="abs" style="left:0;top:2640px" width="1200" height="110" viewBox="0 0 1200 110" aria-hidden="true">
  <path d="M0 95 Q600 -40 1200 95 L1200 110 L0 110Z" fill="#7d7d7f"/>
  <path d="M0 110 Q600 -20 1200 110Z" fill="#000"/>
</svg>

<footer class="abs footer">
  <div class="field" style="left:111px">Name</div>
  <div class="field" style="left:308px">Email</div>
  <div class="field" style="left:505px">Phone</div>
  <div class="field" style="left:702px">Address</div>
  <div class="subscribe">Subscribe</div>

  <div class="brand"><span class="dot"></span>brightpath</div>
  <p class="abs about-foot">BrightPath Care Clinics is focused on our patients first. Connect with us to stay up to date with current news and upcoming events.</p>

  <div class="abs col" style="left:433px;top:156px">
    <h5>Quick Links</h5>
    <ul><li>&gt;&gt; Home</li><li>&gt;&gt; About Us</li><li>&gt;&gt; Locations</li><li>&gt;&gt; For Patients</li><li>&gt;&gt; For Providers</li><li>&gt;&gt; Book Online</li></ul>
  </div>
  <div class="abs col" style="left:639px;top:156px">
    <h5>Other Links</h5>
    <ul><li>&gt;&gt; Terms &amp; Condition</li><li>&gt;&gt; Privacy Policy</li><li>&gt;&gt; FAQ</li><li>&gt;&gt; Acceptable Use</li></ul>
  </div>
  <div class="abs col" style="left:853px;top:156px;width:250px">
    <h5>Contact Us</h5>
    <div class="contact-row"><i><svg viewBox="0 0 24 24"><path d="M6.6 10.8a15 15 0 0 0 6.6 6.6l2.2-2.2a1 1 0 0 1 1-.25 11.4 11.4 0 0 0 3.6.57 1 1 0 0 1 1 1V20a1 1 0 0 1-1 1A17 17 0 0 1 3 4a1 1 0 0 1 1-1h3.5a1 1 0 0 1 1 1c0 1.25.2 2.45.57 3.57a1 1 0 0 1-.25 1z"/></svg></i><span>Phone: 604.555.0147</span></div>
    <div class="contact-row"><i><svg viewBox="0 0 24 24"><path d="M12 2a7 7 0 0 0-7 7c0 5 7 13 7 13s7-8 7-13a7 7 0 0 0-7-7zm0 9.5A2.5 2.5 0 1 1 12 6.5a2.5 2.5 0 0 1 0 5z"/></svg></i><span>BrightPath Care Clinics,<br>Canada.</span></div>
    <div class="contact-row"><i><svg viewBox="0 0 24 24"><path d="M3 5h18v14H3z"/></svg></i><span>hello@brightpathcareclinics.ca</span></div>
  </div>

  <div class="abs rule"></div>
  <p class="abs copy">Copyrights@2022.BrightPath Care Clinics.All Rights Reserved</p>
</footer>

</body>
</html>
```